Duct Manufacturing Company new to the industry needs business card and stationary design

we are sheet metal duct manufacturers looking for a business card design to fit my new business logo.
nothing to crazy that will date, but want it to stand out from the crowed.
I'm sure you guys will work it out.

Contact Information for Business Card

Glen Marsh
Director

Address
17 Dorwell St
Carlowe NSW 2815

0438 760 514

Sales@flowbend.com.au

Font styles to use
Other font styles liked:
• BankGothic md bt

Requirements
Nice to have
• Like the idea of corner rounded to match logo
• like to keep colours flowing
• font I like sharp square not rounded

```html
<!DOCTYPE html>
<html lang="en">
<head>
<meta charset="utf-8">
<title>Flowbend Industries – Business Card</title>
<link href="https://fonts.googleapis.com/css2?family=Montserrat:wght@400;500;700;800&display=swap" rel="stylesheet">
<style>
  :root{
    --stage:#dcdcdc;
    --card:#ffffff;
    --blue-light:#1f8fd6;
    --blue-dark:#0b3f8c;
    --green:#5cb82e;
    --green-dark:#2f9a2a;
    --ink:#ffffff;
  }
  html,body{margin:0;padding:0;width:1200px;height:1200px;overflow:hidden;background:var(--stage);font-family:"Montserrat",sans-serif;}
  .canvas{position:relative;width:1200px;height:1200px;}
  .card{position:absolute;left:220px;width:760px;height:434px;background:var(--card);border-radius:28px;overflow:hidden;box-shadow:0 10px 24px rgba(0,0,0,.18);}
  .card--front{top:120px;}
  .card--back{top:636px;}
  .card__art{position:absolute;inset:0;width:100%;height:100%;}
  .wordmark{position:absolute;display:flex;align-items:center;gap:14px;color:var(--green);font-weight:800;letter-spacing:.04em;line-height:1.05;}
  .wordmark__dot{width:34px;height:34px;border-radius:50%;background:var(--green);flex:none;}
  .wordmark__name{font-size:38px;}
  .wordmark__name span{display:block;font-size:22px;letter-spacing:.28em;}
  .card--front .wordmark{left:0;right:0;top:160px;justify-content:center;}
  .card--back .wordmark{left:40px;top:170px;}
  .card--back .wordmark__name{font-size:32px;}
  .card--back .wordmark__name span{font-size:18px;}
  .contact{position:absolute;left:500px;top:92px;color:var(--ink);}
  .contact__name{margin:0;font-size:27px;font-weight:700;letter-spacing:.12em;text-transform:uppercase;}
  .contact__role{margin:2px 0 24px;font-size:15px;font-weight:400;}
  .contact__list{list-style:none;margin:0;padding:0;font-size:17px;font-weight:400;}
  .contact__list li{display:flex;align-items:flex-start;gap:12px;margin-bottom:8px;}
  .contact__list svg{width:16px;height:16px;flex:none;margin-top:3px;fill:var(--ink);}
</style>
</head>
<body>
<main class="canvas">

  <section class="card card--front" aria-label="Card front">
    <svg class="card__art" viewBox="0 0 760 434" preserveAspectRatio="none" aria-hidden="true">
      <defs>
        <linearGradient id="frontBlue" x1="0" x2="1"><stop offset="0" stop-color="var(--blue-light)"/><stop offset="1" stop-color="var(--blue-dark)"/></linearGradient>
        <linearGradient id="frontGreen" x1="0" x2="1"><stop offset="0" stop-color="var(--green-dark)"/><stop offset="1" stop-color="var(--green)"/></linearGradient>
      </defs>
      <path d="M0 418 L560 418 L600 400 L760 400 L760 434 L0 434 Z" fill="url(#frontGreen)"/>
      <path d="M600 400 L760 400 L760 434 L560 434 Z" fill="url(#frontBlue)"/>
    </svg>
    <div class="wordmark">
      <div class="wordmark__dot"></div>
      <div class="wordmark__name">FLOWBEND<span>INDUSTRIES</span></div>
    </div>
  </section>

  <section class="card card--back" aria-label="Card back">
    <svg class="card__art" viewBox="0 0 760 434" preserveAspectRatio="none" aria-hidden="true">
      <defs>
        <linearGradient id="backBlue" x1="0" y1="0" x2="1" y2="1"><stop offset="0" stop-color="var(--blue-light)"/><stop offset="1" stop-color="var(--blue-dark)"/></linearGradient>
      </defs>
      <path d="M250 0 C390 25 440 180 430 300 C445 190 400 40 290 0 Z" fill="var(--green)"/>
      <path d="M300 0 C420 40 470 240 440 434 L760 434 L760 0 Z" fill="url(#backBlue)"/>
    </svg>
    <div class="wordmark">
      <div class="wordmark__dot"></div>
      <div class="wordmark__name">FLOWBEND<span>INDUSTRIES</span></div>
    </div>
    <div class="contact">
      <h1 class="contact__name">Glen Marsh</h1>
      <p class="contact__role">Director</p>
      <ul class="contact__list">
        <li><svg viewBox="0 0 16 16"><path d="M3 1h3l1.5 4-2 1.2a9 9 0 0 0 4.3 4.3L11 8.5l4 1.5v3a2 2 0 0 1-2 2C6.5 15 1 9.5 1 3a2 2 0 0 1 2-2z"/></svg>0438 760 514</li>
        <li><svg viewBox="0 0 16 16"><path d="M8 1a7 7 0 1 0 0 14A7 7 0 0 0 8 1zm0 1.5c.8 0 1.8 1.6 2.1 4H5.9C6.2 4.1 7.2 2.5 8 2.5zM2.6 7.5h1.8c0-.4.1-1 .2-1.6a5.6 5.6 0 0 0-2 1.6zm0 1h2c.1.8.3 1.6.5 2.3a5.5 5.5 0 0 1-2.5-2.3zm3.3 0h4.2c-.3 2.4-1.3 4-2.1 4s-1.8-1.6-2.1-4zm5.6 0h2a5.5 5.5 0 0 1-2.5 2.3c.3-.7.5-1.5.5-2.3zm0-1c0-.6-.1-1.2-.2-1.6a5.6 5.6 0 0 1 2 1.6z"/></svg>flowbend.com.au</li>
        <li><svg viewBox="0 0 16 16"><path d="M1 3h14v10H1zm1.5 1.2V5l5.5 4 5.5-4v-.8z"/></svg>sales@flowbend.com.au</li>
        <li><svg viewBox="0 0 16 16"><path d="M8 1a5 5 0 0 0-5 5c0 3.8 5 9 5 9s5-5.2 5-9a5 5 0 0 0-5-5zm0 7a2 2 0 1 1 0-4 2 2 0 0 1 0 4z"/></svg><span>17 Dorwell St<br>Carlowe NSW 2815</span></li>
      </ul>
    </div>
  </section>

</main>
</body>
</html>
```